Verdant Systems Business Card

want the back of card to be blue- with the logo in the center
front of card- info plus logo (info being mailing address, email address, and website address )
4 different names with titles to have on cards
1) Calvin Borsted - Owner
2) Naomi Trelvik- Customer Relationship Specialist
3) Felix Andrade- Vice President of Sales
4) Owen Markby- Chief Technology Officer

Target Market(s)

tech company in the government/probation office industry

Industry/Entity Type

Government Office

Contact Information for Business Card

1) Calvin Borsted - Owner

Colors
0355a3
ffffff

Requirements
Must have
• back side should be blue, with the logo placed in the center
• front side needs to include both the logo, as well as company info (info should include website address, email address, and mailing address)

```html
<!DOCTYPE html>
<html lang="en">
<head>
<meta charset="utf-8">
<title>Verdant Systems Business Card</title>
<link href="https://fonts.googleapis.com/css2?family=Roboto:wght@400;500;700&display=swap" rel="stylesheet">
<style>
  :root {
    --stage: #e8e8eb;
    --navy: #172c55;
    --navy-ink: #1c3262;
    --divider: #5c6678;
    --paper: #f6f6f7;
    --white: #ffffff;
    --rule: rgba(255, 255, 255, 0.35);
  }
  * { margin: 0; padding: 0; box-sizing: border-box; }
  html, body {
    width: 1200px;
    height: 900px;
    overflow: hidden;
    background: var(--stage);
    font-family: "Roboto", Arial, sans-serif;
  }
  .card {
    position: absolute;
    left: 112px;
    top: 148px;
    width: 976px;
    height: 604px;
    display: flex;
    box-shadow: 0 10px 30px rgba(0, 0, 0, 0.12);
  }
  .card-info {
    width: 510px;
    height: 100%;
    background: var(--navy);
    color: var(--white);
    padding: 50px 36px 0 50px;
  }
  .card-divider {
    width: 9px;
    height: 100%;
    background: var(--divider);
  }
  .card-brand {
    flex: 1;
    height: 100%;
    background: var(--paper);
    display: flex;
    flex-direction: column;
    align-items: center;
    justify-content: center;
  }
  .person { margin-bottom: 14px; }
  .person-name {
    font-size: 34px;
    font-weight: 700;
    line-height: 1.1;
    text-transform: uppercase;
    letter-spacing: 0.2px;
  }
  .person-title {
    font-size: 26px;
    font-weight: 400;
    line-height: 1.15;
    opacity: 0.92;
  }
  .contact {
    border-top: 1px solid var(--rule);
    margin-top: 22px;
    padding-top: 10px;
    font-size: 26px;
    line-height: 1.4;
  }
  .contact + .contact { margin-top: 10px; }
  .brand-mark {
    width: 60px;
    height: 60px;
    background: var(--navy-ink);
    margin-bottom: 26px;
  }
  .brand-name {
    color: var(--navy-ink);
    font-size: 46px;
    font-weight: 500;
    line-height: 1.15;
    text-align: center;
    text-transform: uppercase;
    letter-spacing: 2px;
  }
</style>
</head>
<body>
  <main class="card">
    <section class="card-info">
      <div class="person">
        <div class="person-name">Calvin Borsted</div>
        <div class="person-title">Owner</div>
      </div>
      <div class="person">
        <div class="person-name">Naomi Trelvik</div>
        <div class="person-title">Customer Relationship Specialist</div>
      </div>
      <div class="person">
        <div class="person-name">Felix Andrade</div>
        <div class="person-title">Vice President of Sales</div>
      </div>
      <div class="person">
        <div class="person-name">Owen Markby</div>
        <div class="person-title">Chief Technology Officer</div>
      </div>
      <div class="contact">
        <div>support@VerdantSystems.com</div>
        <div>www.VerdantSystems.com</div>
      </div>
      <div class="contact">
        <div>421, Address line here,</div>
        <div>45452,Country Name</div>
      </div>
    </section>
    <div class="card-divider"></div>
    <section class="card-brand">
      <div class="brand-mark"></div>
      <div class="brand-name">Verdant<br>Systems</div>
    </section>
  </main>
</body>
</html>
```